High-end Oceanfront Real Estate Group Needs Clean, Modern Web Design

I’m looking for a clean, professional, modern and beautiful homepage web design for a Real Estate group in Southern California, USA.

The group/company is “Marwick on the Shore,” and they specialize in high end (i.e. expensive), oceanfront real estate in the Orange County area.

The look and feel of the page should accentuate the brand qualities: luxurious/expensive, professional, and beautiful (Orange County is one of the most beautiful areas in all the US and we would love the site to emphasize the beautiful beaches and scenery it has to offer).

Looks we like:
• www.brantleyhomesrealty.example
• www.closedbyvane.example -- I think the design is pretty out-dated in this site, but I like the organization/layout of the site

Header Tags (I don’t know if we can fit all of these, may need a side-menu, but I’d prefer header title only if possible):
• Welcome
• Featured Listings
• Previously Sold
• Sell
• Property Search
• Team
• Videos
• Blog
• Explore O.C.
• Contact

I have attached the beach and logo pics that we would like to use as the header, a few pictures of the team, and one sample home/view pic which can be used in any of the other sections (for pictures of the homes, just find expensive oceanfront houses and that will be fine).

I promise to provide feedback to each and every design submission. I appreciate the hard work that all of you are putting into your designs. There can be only one contest winner, but I hope to give all of you helpful feedback to submit the best designs possible!

Target Market(s)

Very wealthy home owners of oceanfront properties. These properties are worth several millions of dollars, and thus the site and brand needs to be targeted to very wealthy, successful individuals and families (both US and international buyers).

Industry/Entity Type

Real Estate

Number of Pages Required

2 page

Requirements
Must have
• I don’t want to give too many requirements, because I want to let you all be creative. However, here are the few Must Haves:
• Must submit 2 page designs (a home page and a sub page)
• Must use logo provided
• Focus is mostly on homes, but I would like to include some beach/ocean imagery as well
• The first “item” on the home page should be an accordion/slider which shows pictures of homes and with 1 line of text: “List with the Leader” and two link buttons: “Sell Your Home” and “Buy Your Home”
• Color palette needs to be mainly blues--to match ocean and sky blue
• Exported in all major formats (psd,ai,eps,png,jpeg,etc)
Nice to have
• We don’t necessarily need all of these, but would like to feature most:
• List of videos
• “Meet the Team”—brief team bios and pics
• Link(s) to Blog
• “List with the Leader” – section on why they should choose this firm
• Featured Listings
• Previously Sold

```html
<!DOCTYPE html>
<html lang="en">
<head>
<meta charset="utf-8">
<title>Marwick on the Shore — Oceanfront Real Estate</title>
<link href="https://fonts.googleapis.com/css2?family=Raleway:ital,wght@0,200;0,300;0,400;0,500;0,600;1,400;1,500&family=Lora:ital@1&display=swap" rel="stylesheet">
<style>
:root{
  --blue:#29a9e8;
  --blue-dark:#1d8fd0;
  --ink:#333;
  --muted:#777;
  --rule:#e4e4e4;
  --side:#f3f3f3;
  --footer:#171b22;
  --footer-text:#8f96a0;
  --white:#fff;
}
*{box-sizing:border-box;margin:0;padding:0}
html,body{width:1200px;height:2209px;overflow:hidden;background:var(--white)}
body{font-family:"Raleway",sans-serif;color:var(--ink);position:relative}
.page{position:relative;width:1200px;height:2209px}
.abs{position:absolute}

/* hero */
.hero{left:0;top:0;width:1200px;height:608px;
  background:linear-gradient(180deg,#3f66a8 0%,#7e9bc8 28%,#a9bcd6 42%,#3b6a5a 56%,#2f4a33 72%,#5d6a52 100%)}
.hero-title{left:314px;width:886px;top:230px;text-align:center;color:var(--white);
  font-weight:300;font-size:45px;letter-spacing:2px}
.btn{display:flex;align-items:center;justify-content:center;font-weight:600;font-size:16px;color:var(--white);letter-spacing:.5px}
.btn-sell{left:515px;top:315px;width:180px;height:44px;background:var(--blue)}
.btn-buy{left:711px;top:315px;width:181px;height:44px;border:2px solid var(--white)}
.arrow{top:298px;width:36px;height:45px;background:rgba(20,20,20,.75);display:flex;align-items:center;justify-content:center}
.arrow-left{left:0}
.arrow-right{right:0}

/* sidebar */
.sidebar{left:99px;top:0;width:215px;height:1936px;background:var(--side)}
.sidebar-top{left:99px;top:0;width:215px;height:608px;background:rgba(238,241,245,.88)}
.brand{left:99px;top:0;width:215px;height:140px;display:flex;align-items:center;justify-content:center}
.brand-name{font-weight:300;font-size:27px;line-height:1.15;color:#3a4a6b;text-align:center;letter-spacing:1px}
.nav{left:99px;top:140px;width:215px;list-style:none}
.nav li{height:41px;display:flex;align-items:center;padding-left:20px;font-size:13px;color:#333;border-bottom:1px solid rgba(0,0,0,.06)}
.nav li.active{background:var(--blue);color:var(--white);height:46px}
.side-head{left:99px;width:215px;height:40px;background:var(--blue);color:var(--white);
  display:flex;align-items:center;justify-content:center;font-size:16px;letter-spacing:.5px}
.blog-item{left:99px;width:215px;padding:0 18px 0 17px;border-bottom:1px solid var(--rule);height:85px;padding-top:12px}
.blog-item p{font-size:12.5px;color:var(--muted);line-height:1.4}
.blog-item time{display:block;margin-top:6px;font-size:11.5px;font-weight:600;color:var(--blue);padding-left:3px}
.side-link{left:122px;font-size:12px;font-weight:500;color:#222}
.side-quote{left:117px;width:190px;font-family:"Lora",serif;font-style:italic;font-size:15px;color:#666;line-height:1.4}
.side-photo{left:117px;width:178px;border:3px solid #ddd}
.side-text{left:117px;width:185px;font-size:12px;color:#666;line-height:1.6}
.price{color:var(--blue);font-style:italic;font-weight:600}

/* main */
.section-title{left:355px;font-weight:400;font-size:23px;color:#333;letter-spacing:.5px}
.section-intro{left:355px;width:750px;font-size:15.5px;color:#666;line-height:1.5}
.rule{left:353px;width:748px;height:1px;background:var(--rule)}
.video{left:353px;top:751px;width:748px;height:233px;
  background:linear-gradient(180deg,#4f86c6 0%,#a9c7e4 40%,#7cb4c9 62%,#c9a37c 80%,#b98a65 100%)}
.play{left:695px;top:826px}
.thumb{top:995px;width:83px;height:68px}
.listing-img{top:1241px;width:231px;height:190px;border:3px solid #e2e2e2}
.listing-body{top:1441px;width:231px;text-align:center}
.listing-body h3{font-weight:400;font-size:15px;color:#222}
.listing-body .meta{font-size:11.5px;color:#aaa;margin-top:4px}
.listing-body .price{display:block;font-size:14px;margin-top:8px}
.btn-more{top:1533px;width:86px;height:35px;background:var(--blue);color:var(--white);font-size:11px;font-weight:600;
  display:flex;align-items:center;justify-content:center;box-shadow:0 3px 0 var(--blue-dark)}
.member-img{top:1748px;width:168px;height:141px;border:3px solid #e2e2e2}
.member{top:1899px;width:168px;text-align:center}
.member h4{font-weight:400;font-size:13px;color:#222}
.member span{display:block;font-style:italic;font-size:12.5px;color:var(--blue)}

/* footer */
.footer{left:0;top:1973px;width:1200px;height:236px;background:var(--footer)}
.foot-head{top:2013px;font-size:13px;font-weight:700;color:var(--blue);letter-spacing:.3px}
.contact-row{left:99px;display:flex;align-items:center;gap:14px;font-size:11px;color:var(--footer-text)}
.contact-row svg{flex:none}
.tweet{left:351px;width:220px;font-size:11px;color:var(--footer-text);line-height:1.5}
.tweet time{display:block;color:var(--blue);font-style:italic;font-size:10px}
.about-list{left:665px;top:2044px;list-style:none}
.about-list li{font-size:11px;color:var(--footer-text);height:24px}
.follow-text{left:927px;top:2057px;width:170px;font-size:11px;color:var(--footer-text);line-height:1.5}
.socials{left:927px;top:2126px;display:flex;gap:10px}
.socials span{width:19px;height:19px;border-radius:50%;background:#3a4048}
.socials span.on{background:#e8e8e8}
.copyright{left:932px;top:2168px;font-size:10px;color:#ddd}
</style>
</head>
<body>
<div class="page">

  <!-- hero slider -->
  <div class="abs hero" role="img" aria-label="Oceanfront resort with palm trees, gardens and a blue sky with clouds"></div>
  <h1 class="abs hero-title">LIST WITH THE LEADER</h1>
  <a class="abs btn btn-sell">SELL YOUR HOME</a>
  <a class="abs btn btn-buy">BUY YOUR HOME</a>
  <div class="abs arrow arrow-left"><svg width="12" height="18" viewBox="0 0 12 18"><path d="M10 2 3 9l7 7" fill="none" stroke="#fff" stroke-width="2.5"/></svg></div>
  <div class="abs arrow arrow-right"><svg width="12" height="18" viewBox="0 0 12 18"><path d="M2 2l7 7-7 7" fill="none" stroke="#fff" stroke-width="2.5"/></svg></div>

  <!-- sidebar -->
  <aside>
    <div class="abs sidebar"></div>
    <div class="abs sidebar-top"></div>
    <div class="abs brand"><div class="brand-name">MARWICK<br>ON THE SHORE</div></div>
    <ul class="abs nav">
      <li class="active">• WELCOME</li>
      <li>• FEATURED LISTINGS</li>
      <li>• PREVIOUSLY SOLD</li>
      <li>• SELL</li>
      <li>• PROPERTY SEARCH</li>
      <li>• TEAM</li>
      <li>• VIDEOS</li>
      <li>• BLOG</li>
      <li>• EXPLORE O.C.</li>
      <li>• CONTACT</li>
    </ul>

    <div class="abs side-head" style="top:608px">OUR BLOG</div>
    <div class="abs blog-item" style="top:648px"><p>Sed ut pers lore piciatis unde omnis iste naloretus error</p><time>Feb 27, 2015</time></div>
    <div class="abs blog-item" style="top:733px"><p>Sed ut pers lore piciatis unde omnis iste naloretus error</p><time>Feb 27, 2015</time></div>
    <div class="abs blog-item" style="top:818px;border-bottom:0"><p>Sed ut pers lore piciatis unde omnis iste naloretus error</p><time>Feb 27, 2015</time></div>
    <div class="abs side-link" style="top:915px">READ MORE</div>

    <div class="abs side-head" style="top:950px">LIST WITH THE LEADER</div>
    <p class="abs side-quote" style="top:1007px">Why they should choose this firm???</p>
    <div class="abs side-photo" style="top:1064px;height:124px;background:linear-gradient(180deg,#e8dfcf,#8a5e3f 60%,#c27a5a)" role="img" aria-label="Home gym interior with exercise equipment"></div>
    <p class="abs side-text" style="top:1207px">lorem ipsum dolor sit amet, consectetur adipiscing elit. Ut volutpat rutrum eros sit amet sollicitudin louspendisse.</p>

    <div class="abs side-head" style="top:1305px">PREVIOUSLY SOLD</div>
    <div class="abs side-photo" style="top:1363px;height:124px;background:linear-gradient(180deg,#5a9ad8,#a9d1ee 45%,#2f7fbf 65%,#8ab86a)" role="img" aria-label="Ocean view terrace with pool"></div>
    <p class="abs side-text" style="top:1497px">lorem ipsum dolor sit amet, consectetur <span class="price">$11,888,888</span></p>
    <div class="abs side-photo" style="top:1555px;height:124px;background:linear-gradient(180deg,#c9a98a,#6e4a34 50%,#2f4e9a 80%)" role="img" aria-label="Dining room with chandeliers and blue chairs"></div>
    <p class="abs side-text" style="top:1689px">lorem ipsum dolor sit amet, consectetur <span class="price">$11,888,888</span></p>
    <div class="abs side-photo" style="top:1744px;height:124px;background:linear-gradient(90deg,#8c6f55,#dcd3c4 50%,#7c6450)" role="img" aria-label="Bright living room with tall windows"></div>
    <p class="abs side-text" style="top:1878px">lorem ipsum dolor sit amet, consectetur <span class="price">$11,888,888</span></p>
  </aside>

  <!-- videos -->
  <main>
    <h2 class="abs section-title" style="top:640px">OUR VIDEO'S</h2>
    <p class="abs section-intro" style="top:684px">lorem ipsum dolor sit amet, consectetur adipiscing elit. Ut volutpat rutrum eros sit amet sollicitudin. Suspendisse pulvinar, velit nec pharetar, velit nec pharet ra interdumante.</p>
    <div class="abs video" role="img" aria-label="Beach house with red roof beside the ocean and a pier"></div>
    <svg class="abs play" width="74" height="74" viewBox="0 0 74 74"><circle cx="37" cy="37" r="34" fill="rgba(255,255,255,.25)" stroke="#fff" stroke-width="4"/><circle cx="37" cy="37" r="25" fill="#fff"/><path d="M31 26v22l18-11z" fill="#444"/></svg>
    <div class="abs thumb" style="left:355px;background:linear-gradient(180deg,#6fa5d6,#c05a4a)" role="img" aria-label="Video thumbnail: beach pier"></div>
    <div class="abs thumb" style="left:449px;background:linear-gradient(180deg,#7fb7e0,#3fa9b5)" role="img" aria-label="Video thumbnail: pier over water"></div>
    <div class="abs thumb" style="left:543px;background:linear-gradient(180deg,#8fb0d0,#4f6a52)" role="img" aria-label="Video thumbnail: coastal home"></div>
    <div class="abs thumb" style="left:639px;background:linear-gradient(180deg,#5d8fc4,#a65a4a)" role="img" aria-label="Video thumbnail: house by the sea"></div>
    <div class="abs thumb" style="left:734px;background:linear-gradient(180deg,#cfd8df,#6a7f90)" role="img" aria-label="Video thumbnail: modern interior"></div>
    <div class="abs thumb" style="left:829px;background:linear-gradient(180deg,#9cc07a,#c9a880)" role="img" aria-label="Video thumbnail: family outdoors"></div>
    <div class="abs thumb" style="left:923px;background:linear-gradient(180deg,#6ba0d8,#e0e0d8)" role="img" aria-label="Video thumbnail: sandy beach"></div>
    <div class="abs thumb" style="left:1017px;background:linear-gradient(180deg,#5f9ad0,#b8c4cc)" role="img" aria-label="Video thumbnail: beachfront house"></div>

    <div class="abs rule" style="top:1097px"></div>

    <!-- featured listings -->
    <h2 class="abs section-title" style="top:1120px">FEATURED LISTINGS</h2>
    <p class="abs section-intro" style="top:1164px">lorem ipsum dolor sit amet, consectetur adipiscing elit. Ut volutpat rutrum eros sit amet sollicitudin. Suspendisse pulvinar, velit nec pharetar, velit nec pharet ra interdumante.</p>

    <div class="abs listing-img" style="left:355px;background:linear-gradient(180deg,#7a4a2a,#d4b08a 40%,#6d3a22)" role="img" aria-label="Dining room with ocean view"></div>
    <div class="abs listing-body" style="left:355px"><h3>14 Seacliff Row, Laguna Beach</h3><div class="meta">Bedrooms: 12 &nbsp; Bathrooms: 5 full | 18</div><span class="price">$11,888,888</span></div>
    <a class="abs btn-more" style="left:428px">READ MORE</a>

    <div class="abs listing-img" style="left:613px;background:linear-gradient(180deg,#5b95d0,#d8b777 45%,#4d7a3a)" role="img" aria-label="Luxury villa entrance with fountain"></div>
    <div class="abs listing-body" style="left:613px"><h3>Luxury Real Estate Sales</h3><div class="meta">Bedrooms: 12 &nbsp; Bathrooms: 5 full | 18</div><span class="price">$11,888,888</span></div>
    <a class="abs btn-more" style="left:686px">READ MORE</a>

    <div class="abs listing-img" style="left:869px;background:linear-gradient(180deg,#7fb3e3,#e4d2b4 50%,#6f8d4d)" role="img" aria-label="Large family home with garage"></div>
    <div class="abs listing-body" style="left:869px"><h3>14 Seacliff Row, Laguna Beach</h3><div class="meta">Bedrooms: 12 &nbsp; Bathrooms: 5 full | 18</div><span class="price">$11,888,888</span></div>
    <a class="abs btn-more" style="left:942px">READ MORE</a>

    <div class="abs rule" style="top:1608px"></div>

    <!-- team -->
    <h2 class="abs section-title" style="top:1631px">MEET THE TEAM</h2>
    <p class="abs section-intro" style="top:1675px">lorem ipsum dolor sit amet, consectetur adipiscing elit. Ut volutpat rutrum eros sit amet sollicitudin. Suspendisse pulvinar, velit nec pharetar, velit nec pharet ra interdumante.</p>

    <div class="abs member-img" style="left:355px;background:linear-gradient(180deg,#6b93c8,#d9b9a0)" role="img" aria-label="Portrait of team member"></div>
    <div class="abs member" style="left:355px"><h4>Lena Harwood</h4><span>Sales Partner</span></div>
    <div class="abs member-img" style="left:548px;background:linear-gradient(180deg,#eaeaea,#3a3a3a)" role="img" aria-label="Portrait of team member"></div>
    <div class="abs member" style="left:548px"><h4>Lena Harwood</h4><span>Sales Partner</span></div>
    <div class="abs member-img" style="left:741px;background:linear-gradient(180deg,#dcdcdc,#7d6a60)" role="img" aria-label="Portrait of team member"></div>
    <div class="abs member" style="left:741px"><h4>Lena Harwood</h4><span>Sales Partner</span></div>
    <div class="abs member-img" style="left:934px;background:linear-gradient(180deg,#5a4a3e,#3e3a38)" role="img" aria-label="Portrait of team member"></div>
    <div class="abs member" style="left:934px"><h4>Lena Harwood</h4><span>Sales Partner</span></div>
  </main>

  <!-- footer -->
  <footer>
    <div class="abs footer"></div>
    <h5 class="abs foot-head" style="left:99px">CONTACT US</h5>
    <div class="abs contact-row" style="top:2060px"><svg width="12" height="12" viewBox="0 0 12 12"><path d="M1 3c0-1 1-2 2-2l1 3-1 1c1 2 2 3 4 4l1-1 3 1c0 1-1 2-2 2C5 11 1 7 1 3z" fill="var(--blue)"/></svg>03 5550 0142 (Phone)</div>
    <div class="abs contact-row" style="top:2089px"><svg width="12" height="12" viewBox="0 0 12 12"><rect x="3" y="1" width="6" height="3" fill="var(--blue)"/><rect x="1" y="4" width="10" height="5" rx="1" fill="var(--blue)"/><rect x="3" y="8" width="6" height="3" fill="var(--blue)"/></svg>03 5550 0142 (Fax)</div>
    <div class="abs contact-row" style="top:2118px"><svg width="12" height="10" viewBox="0 0 12 10"><rect width="12" height="10" fill="var(--blue)"/><path d="M0 0l6 5 6-5" fill="none" stroke="var(--footer)" stroke-width="1.2"/></svg><span style="text-decoration:underline">admin@marwickshore.example</span></div>
    <div class="abs contact-row" style="top:2147px;align-items:flex-start"><svg width="10" height="13" viewBox="0 0 10 13"><path d="M5 13S0 7 0 5a5 5 0 0 1 10 0c0 2-5 8-5 8z" fill="var(--blue)"/><circle cx="5" cy="5" r="2" fill="var(--footer)"/></svg><span>PO Box: 4410, Laguna Beach<br>lorem sl3844</span></div>

    <h5 class="abs foot-head" style="left:351px">TWITTER FEED</h5>
    <p class="abs tweet" style="top:2058px">@coastline, Harbor site theme full responsive is coming soon...<time>4 days ago</time></p>
    <p class="abs tweet" style="top:2118px">@coastline, Harbor site theme full responsive is coming soon...<time>4 days ago</time></p>

    <h5 class="abs foot-head" style="left:668px">ABOUT</h5>
    <ul class="abs about-list">
      <li>Investors</li>
      <li>Careers</li>
      <li>Terms &amp; Condtions of Service</li>
      <li>Privacy Policy</li>
      <li>Service Level Agreement</li>
      <li>Master Commercial Agreement</li>
    </ul>

    <h5 class="abs foot-head" style="left:927px">FOLLOW US</h5>
    <p class="abs follow-text">Lorem ipsum dolor sit amet, consectetur adipiscing elit. Nulla in purus nibh. Donec ornare</p>
    <div class="abs socials"><span></span><span class="on"></span><span></span><span></span><span></span></div>
    <p class="abs copyright">Copyright 2015 All Rights Reserved</p>
  </footer>
</div>
</body>
</html>
```